7K packaging design

We are a wholesaler for Automotive Spare Parts in Jordan and Iraq market and we needs to import spare parts from China under our company private brand "7K"
The 7K brand’s product lines include Filtration, Braking Systems, Wheels, Wheel Bolts & Nuts, Shock Absorbers, Sensors, Cooling Systems, Axles and more.
The aim of the project is to unify the brand packaging across all the product lines , we will start by the brake pads then based on the approved design we will do the other products

Target Market(s)

Jordan , Iraq Market

Industry/Entity Type

Automotive spare parts

Requirements
Must have
• Name of the product :Ceramic brake pads specs : Superior stopping power Noise suppression Low Dust Technology Made in china
Nice to have
• Brake pad outline image on the box
Should not have
• Blue color

```html
<!DOCTYPE html>
<html lang="en">
<head>
<meta charset="utf-8">
<title>7K packaging design – dielines</title>
<link href="https://fonts.googleapis.com/css2?family=Exo+2:ital,wght@1,700;1,800&family=Roboto+Condensed:wght@400;700&display=swap" rel="stylesheet">
<style>
  :root{
    --red:#ff0008;
    --red-deep:#8a0006;
    --red-dark:#5a0003;
    --panel-dark:#333333;
    --photo-light:#9a9a9a;
    --photo-dark:#2c2c2c;
    --silver:#e6e6e6;
    --strip:#8c8c8c;
    --white:#ffffff;
    --ink:#1a1a1a;
    --cut:#29abe2;
    --page:#ffffff;
  }
  html,body{margin:0;padding:0;width:980px;height:1200px;overflow:hidden;background:var(--page);}
  .sheet{display:block;width:980px;height:1200px;}
  .cut-line{fill:none;stroke:var(--cut);stroke-width:1.4;}
  .dark-flap{fill:var(--panel-dark);stroke:var(--cut);stroke-width:1;}
  .strip{fill:var(--strip);}
  .silver-band{fill:var(--silver);}
  .title{font-family:"Exo 2",sans-serif;font-style:italic;font-weight:800;fill:var(--white);}
  .brand{font-family:"Exo 2",sans-serif;font-style:italic;font-weight:800;fill:var(--white);}
  .brand-dot{fill:var(--white);opacity:.85;}
  .spec{font-family:"Roboto Condensed",sans-serif;font-weight:400;fill:var(--white);font-size:5px;}
  .spec-icon{fill:none;stroke:var(--white);stroke-width:1.2;}
  .origin{font-family:"Roboto Condensed",sans-serif;font-weight:700;fill:var(--white);}
  .label-box{fill:var(--white);}
  .label-rule{stroke:var(--red);stroke-width:1.5;}
  .label-text{font-family:"Roboto Condensed",sans-serif;fill:var(--ink);}
  .label-qty{font-family:"Roboto Condensed",sans-serif;font-weight:700;fill:var(--red);}
  .art-zone{fill:url(#artShade);}
</style>
</head>
<body>
<svg class="sheet" viewBox="0 0 1737 2126" xmlns="http://www.w3.org/2000/svg" xmlns:xlink="http://www.w3.org/1999/xlink" role="img" aria-label="7K packaging dielines: two ceramic brake pad boxes and an oil filter box">
  <defs>
    <linearGradient id="redTop" x1="0" y1="0" x2="0" y2="1">
      <stop offset="0" stop-color="#5a0003"/><stop offset="1" stop-color="#ff0008"/>
    </linearGradient>
    <linearGradient id="redBottom" x1="0" y1="0" x2="0" y2="1">
      <stop offset="0" stop-color="#ff0008"/><stop offset="1" stop-color="#8a0006"/>
    </linearGradient>
    <linearGradient id="redPanel" x1="0" y1="0" x2="0" y2="1">
      <stop offset="0" stop-color="#ff0008"/><stop offset=".55" stop-color="#d40006"/><stop offset="1" stop-color="#7a0005"/>
    </linearGradient>
    <linearGradient id="redSide" x1="0" y1="0" x2="1" y2="1">
      <stop offset="0" stop-color="#ff0008"/><stop offset=".6" stop-color="#ff0008"/><stop offset="1" stop-color="#8a0006"/>
    </linearGradient>
    <linearGradient id="photoGrey" x1="0" y1="0" x2="1" y2="1">
      <stop offset="0" stop-color="#2c2c2c"/><stop offset=".5" stop-color="#6e6e6e"/><stop offset="1" stop-color="#9a9a9a"/>
    </linearGradient>
    <linearGradient id="artShade" x1="0" y1="0" x2="1" y2="1">
      <stop offset="0" stop-color="#b00006" stop-opacity=".55"/><stop offset="1" stop-color="#5a0003" stop-opacity=".55"/>
    </linearGradient>

    <!-- spec icon row -->
    <g id="specRow">
      <circle class="spec-icon" cx="0" cy="0" r="7"/>
      <text class="spec" x="12" y="-3">SUPERIOR</text>
      <text class="spec" x="12" y="2">STOPPING</text>
      <text class="spec" x="12" y="7">POWER</text>
      <path class="spec-icon" d="M58,-4 h4 l5,-4 v16 l-5,-4 h-4 z"/>
      <text class="spec" x="72" y="-1">NOISE</text>
      <text class="spec" x="72" y="5">SUPPRESSION</text>
      <circle class="spec-icon" cx="121" cy="0" r="6"/>
      <text class="spec" x="131" y="-1">LOW DUST</text>
      <text class="spec" x="131" y="5">TECHNOLOGY</text>
    </g>

    <!-- brake pad box dieline -->
    <g id="brakeBox">
      <!-- top flaps -->
      <rect class="dark-flap" x="48" y="48" width="187" height="161"/>
      <rect class="dark-flap" x="632" y="48" width="188" height="161"/>
      <rect x="235" y="48" width="397" height="161" fill="url(#redTop)" stroke="var(--cut)" stroke-width="1"/>
      <!-- inner lid -->
      <rect class="dark-flap" x="48" y="236" width="187" height="161"/>
      <rect class="dark-flap" x="632" y="236" width="188" height="161"/>
      <rect x="235" y="209" width="397" height="188" fill="url(#redSide)"/>
      <rect class="cut-line" x="108" y="385" width="67" height="12"/>
      <rect class="cut-line" x="692" y="385" width="68" height="12"/>

      <!-- back panel row (upside down) -->
      <rect x="48" y="397" width="187" height="160" fill="url(#photoGrey)" role="img" aria-label="Black and white vehicle photo"/>
      <rect x="235" y="397" width="397" height="160" fill="url(#redPanel)"/>
      <polygon class="strip" points="235,397 510,397 505,428 235,428"/>
      <polygon points="510,397 632,397 632,557 420,557" fill="url(#photoGrey)" role="img" aria-label="Black and white vehicle photo"/>
      <polygon class="silver-band" points="500,397 510,397 428,557 418,557"/>
      <rect class="art-zone" x="250" y="435" width="170" height="112" role="img" aria-label="Brake pad outline illustration"/>
      <g transform="rotate(180 370 412)">
        <use href="#specRow" x="260" y="412"/>
      </g>
      <g transform="rotate(180 578 440)">
        <text class="title" x="540" y="430" font-size="19">Ceramic</text>
        <text class="title" x="540" y="448" font-size="19">Brake</text>
        <text class="title" x="540" y="466" font-size="19">Pads</text>
      </g>
      <g transform="rotate(180 595 523)">
        <circle class="brand-dot" cx="572" cy="523" r="6"/>
        <text class="brand" x="582" y="534" font-size="30">7K</text>
      </g>

      <rect x="632" y="397" width="188" height="160" fill="url(#photoGrey)" role="img" aria-label="Black and white vehicle photo"/>
      <g transform="rotate(180 726 440)">
        <text class="title" x="726" y="440" font-size="14" text-anchor="middle">Ceramic Brake Pads</text>
        <text class="origin" x="726" y="469" font-size="8" text-anchor="middle">MADE IN CHINA</text>
      </g>
      <g transform="rotate(180 726 512)">
        <circle class="brand-dot" cx="694" cy="512" r="8"/>
        <text class="brand" x="708" y="527" font-size="42">7K</text>
      </g>

      <!-- front panel row -->
      <rect x="48" y="557" width="187" height="154" fill="url(#redSide)"/>
      <rect x="632" y="557" width="188" height="154" fill="url(#redSide)"/>
      <rect x="235" y="557" width="397" height="187" fill="url(#redPanel)"/>
      <rect class="cut-line" x="105" y="711" width="73" height="7"/>
      <rect class="cut-line" x="692" y="711" width="70" height="7"/>
      <circle class="brand-dot" cx="262" cy="602" r="8"/>
      <text class="brand" x="276" y="618" font-size="44">7K</text>
      <text class="title" x="255" y="673" font-size="17">Ceramic Brake Pads</text>
      <rect class="art-zone" x="418" y="585" width="195" height="130" role="img" aria-label="Brake pad outline illustration"/>
      <use href="#specRow" x="262" y="711"/>

      <!-- bottom flaps -->
      <path d="M235,744 L122,744 Q92,744 94,790 Q108,880 190,903 L235,905 Z" fill="url(#redSide)" stroke="var(--cut)" stroke-width="1"/>
      <path d="M632,744 L745,744 Q775,744 773,790 Q759,880 677,903 L632,905 Z" fill="url(#redSide)" stroke="var(--cut)" stroke-width="1"/>
      <rect x="235" y="744" width="397" height="161" fill="url(#redPanel)"/>
      <polygon points="235,744 445,744 360,905 235,905" fill="url(#photoGrey)" role="img" aria-label="Black and white vehicle photo"/>
      <polygon class="silver-band" points="440,744 450,744 365,905 355,905"/>
      <polygon class="strip" points="378,875 632,875 632,905 362,905"/>
      <rect class="art-zone" x="445" y="755" width="170" height="110" role="img" aria-label="Brake pad outline illustration"/>
      <circle class="brand-dot" cx="258" cy="780" r="6"/>
      <text class="brand" x="268" y="792" font-size="32">7K</text>
      <text class="title" x="248" y="852" font-size="18">Ceramic</text>
      <text class="title" x="248" y="868" font-size="18">Brake</text>
      <text class="title" x="248" y="884" font-size="18">Pads</text>
      <use href="#specRow" x="420" y="890"/>
    </g>

    <!-- oil filter panel heading -->
    <g id="filterHead">
      <circle class="brand-dot" cx="28" cy="1488" r="9"/>
      <text class="brand" x="42" y="1508" font-size="56">7K</text>
      <text class="title" x="155" y="1484" font-size="27">Takes</text>
      <text class="title" x="152" y="1507" font-size="27">you miles</text>
    </g>
  </defs>

  <!-- brake pad boxes -->
  <use href="#brakeBox"/>
  <use href="#brakeBox" x="868"/>

  <!-- oil filter box: dieline -->
  <g class="filter-dieline">
    <path class="cut-line" d="M295,1435 L230,1450 L230,1745 L295,1808"/>
    <path class="cut-line" d="M598,1292 L708,1292 M738,1292 L850,1292 Q862,1292 866,1305 L884,1390 L900,1405 L902,1435"/>
    <path class="cut-line" d="M1506,1435 L1506,1292 L1398,1292 M1368,1292 L1255,1292 Q1243,1292 1240,1305 L1222,1390 L1208,1405 L1205,1435"/>
    <path class="cut-line" d="M298,1808 L312,2010 Q314,2020 325,2020 L372,2020 L445,1960 L510,2020 L572,2020 Q582,2020 582,2008 L590,1835 L575,1830 L448,1960"/>
    <path class="cut-line" d="M598,1808 L658,1948 Q665,1960 680,1960 L750,1960 L902,1808"/>
    <path class="cut-line" d="M905,1808 L918,2010 Q920,2020 932,2020 L980,2020 L1055,1960 L1115,2020 L1178,2020 Q1188,2020 1188,2008 L1195,1835 L1182,1830 L1055,1960"/>
    <path class="cut-line" d="M1210,1808 L1265,1948 Q1272,1960 1288,1960 L1358,1960 L1506,1808"/>
  </g>

  <!-- oil filter top lid -->
  <rect x="295" y="1058" width="303" height="377" fill="url(#redTop)"/>
  <polygon points="295,1258 598,1285 598,1435 295,1435" fill="url(#photoGrey)" role="img" aria-label="Black and white truck photo"/>
  <polygon class="silver-band" points="295,1250 598,1277 598,1287 295,1260"/>
  <g transform="rotate(180 446 1195)">
    <text class="title" x="446" y="1212" font-size="40" text-anchor="middle">Oil Filter</text>
    <text class="title" x="446" y="1232" font-size="15" text-anchor="middle">Premium Quality</text>
  </g>
  <g transform="rotate(180 440 1350)">
    <text class="title" x="312" y="1335" font-size="25">Takes</text>
    <text class="title" x="312" y="1360" font-size="25">you miles</text>
    <circle class="brand-dot" cx="470" cy="1348" r="9"/>
    <text class="brand" x="486" y="1372" font-size="64">7K</text>
  </g>

  <!-- panel 1 -->
  <rect x="295" y="1435" width="303" height="373" fill="url(#redPanel)"/>
  <use href="#filterHead" x="295"/>
  <text class="title" x="446" y="1580" font-size="42" text-anchor="middle">Oil Filter</text>
  <text class="title" x="446" y="1598" font-size="15" text-anchor="middle">Premium Quality</text>
  <rect class="art-zone" x="368" y="1612" width="158" height="160" role="img" aria-label="Oil filter outline illustration"/>
  <text class="origin" x="446" y="1794" font-size="11" text-anchor="middle">MADE IN KOREA</text>

  <!-- panel 2 -->
  <rect x="598" y="1435" width="304" height="373" fill="url(#redPanel)"/>
  <polygon points="598,1435 902,1435 902,1585 598,1555" fill="url(#photoGrey)" role="img" aria-label="Black and white truck photo"/>
  <polygon class="silver-band" points="598,1553 902,1583 902,1591 598,1561"/>
  <use href="#filterHead" x="598"/>
  <text class="title" x="750" y="1622" font-size="42" text-anchor="middle">Oil Filter</text>
  <text class="title" x="750" y="1640" font-size="15" text-anchor="middle">Premium Quality</text>
  <rect class="art-zone" x="688" y="1652" width="126" height="125" role="img" aria-label="Oil filter outline illustration"/>
  <text class="origin" x="750" y="1794" font-size="11" text-anchor="middle">MADE IN KOREA</text>

  <!-- panel 3 -->
  <rect x="902" y="1435" width="303" height="373" fill="url(#redPanel)"/>
  <use href="#filterHead" x="902"/>
  <text class="title" x="1054" y="1600" font-size="42" text-anchor="middle">Oil Filter</text>
  <text class="title" x="1054" y="1618" font-size="15" text-anchor="middle">Premium Quality</text>
  <rect class="label-box" x="958" y="1650" width="192" height="120" rx="6"/>
  <text class="label-text" x="970" y="1666" font-size="12" font-weight="700">ELEMENT, OIL</text>
  <line class="label-rule" x1="966" y1="1671" x2="1143" y2="1671"/>
  <text class="label-text" x="1054" y="1698" font-size="22" text-anchor="middle">70815-20004</text>
  <text class="label-text" x="1020" y="1747" font-size="6" font-weight="700">QTY:</text>
  <text class="label-qty" x="1050" y="1749" font-size="16">1</text>
  <text class="label-text" x="1054" y="1764" font-size="13" font-weight="700" text-anchor="middle">MADE IN KOREA</text>

  <!-- panel 4 -->
  <rect x="1205" y="1435" width="301" height="373" fill="url(#redPanel)"/>
  <polygon points="1205,1435 1506,1435 1506,1588 1205,1558" fill="url(#photoGrey)" role="img" aria-label="Black and white truck photo"/>
  <polygon class="silver-band" points="1205,1556 1506,1586 1506,1594 1205,1564"/>
  <use href="#filterHead" x="1205"/>
  <text class="title" x="1355" y="1624" font-size="42" text-anchor="middle">Oil Filter</text>
  <text class="title" x="1355" y="1642" font-size="15" text-anchor="middle">Premium Quality</text>
  <rect class="art-zone" x="1293" y="1652" width="126" height="125" role="img" aria-label="Oil filter outline illustration"/>
  <text class="origin" x="1355" y="1794" font-size="11" text-anchor="middle">MADE IN KOREA</text>
</svg>
</body>
</html>
```